Hi Designers,

I will need 4 web pages designed. The web page looks like an App (if you click on the logo, or the icon on an iPad, it will take you to the website), but it is still a webpage.

Please check the attachment on this brief to understand what specific pages I need to be designed.

A .PSD (straight-up PhotoShop image) as final deliverable is fine, as long as you give us the exact “web color numbers”.

The design is for desktop and iPad but in a single unified web application, NOT separate web app and (native) iPad app.

Details:

Brightwater Policy Partners is developing a browser-based application for use on any mobile device or desktop. The app will be used by corporations to communicate with their employees regarding legal, regulatory and company requirements for conducting business. The app is known as “Harbor Guidance Portal.” When the user clicks on the icon for Harbor Guidance Portal, they will enter a site full of information that a company deems necessary for the employee to do his/her job. There are several content sections within the site, including a login page, training, policies, forms, news feeds and blogs.

The application has been built using Microsoft .NET, and fully supports CSS-type skinning; it uses traditional page layouts. We are seeking a product logo concept (image), a master application/desktop icon (image), as well as a full color scheme/theme/skin design for all areas of the application (header area, body text, menu bar, etc.) in the form of a CSS. The look should be clean, crisp and professional; nothing cartoony or whimsical. It should be easy to read and “airy”.

We have sketched prototypes for the basic application page layout that we can send as a next step of the process.
Updates

Screen shots have been uploaded to this project.  Please use them to guide your design.

Dear designers,

I apologize for the delay in providing feedback. My partners and I will provide feedback in a few days. Thank you for your patience.

Industry/Entity Type

Business

Font styles to use
Other font styles liked:
• see font on screen shots when uploaded

```html
<!DOCTYPE html>
<html lang="en">
<head>
<meta charset="utf-8">
<title>Harbor Guidance Portal</title>
<link rel="stylesheet" href="https://fonts.googleapis.com/css2?family=Source+Sans+3:wght@400;600&display=swap">
<style>
:root{
  --page:#efefef;
  --card:#ffffff;
  --line:#e1e1e1;
  --text:#7a7a7a;
  --dark:#3c3c3c;
  --blue:#2f7ed3;
  --brand:#2b5c9c;
  --navy:#1d5597;
  --blue-top:#3f82cc;
  --green:#55a51f;
  --orange:#f39200;
  --footer:#2a2a2a;
  --white:#ffffff;
}
*{box-sizing:border-box;margin:0;padding:0}
html,body{width:1115px;height:1200px;overflow:hidden;background:var(--page)}
body{font-family:"Source Sans 3",sans-serif;color:var(--text)}
.stage{position:relative;width:1200px;height:1291px;transform:scale(.92917);transform-origin:0 0;background:var(--page)}
.abs{position:absolute}
a{color:inherit;text-decoration:none}

/* header */
.brand{left:131px;top:34px;display:flex;align-items:center;gap:10px}
.brand-mark{width:34px;height:34px;border-radius:50%;background:var(--brand)}
.brand-name{color:var(--brand);font-size:18px;line-height:23px;font-weight:400;text-transform:uppercase}
.topnav{right:345px;top:37px;display:flex;align-items:center;font-size:13px;color:var(--dark)}
.topnav a{display:flex;align-items:center;gap:7px}
.topnav a.current{color:var(--navy)}
.topnav .sep{margin:0 10px;color:#888}
.search{left:876px;top:28px;width:194px;height:31px;background:#fff;border:1px solid var(--line);border-radius:3px;display:flex;align-items:center;justify-content:space-between;padding-left:13px;font-size:11px;font-style:italic;color:#aaa}
.search .go{width:34px;height:100%;border-left:1px solid var(--line);display:flex;align-items:center;justify-content:center}
.notify{left:822px;top:90px;width:87px;height:32px;border-radius:3px;background:linear-gradient(var(--blue-top),var(--navy));display:flex;align-items:center;gap:12px;padding-left:13px;color:#fff;font-size:15px}
.notify .count{width:18px;height:18px;border-radius:50%;background:#fff;color:var(--navy);font-size:11px;display:flex;align-items:center;justify-content:center}
.user{left:920px;top:89px;width:150px;height:33px;background:#fff;border:1px solid var(--line);border-radius:3px;display:flex;align-items:center;font-size:12px;color:var(--dark)}
.avatar{width:26px;height:26px;margin:0 12px 0 2px;background:linear-gradient(135deg,#8b7a70,#4d4a52)}
.user .caret{margin-left:auto;width:29px;height:20px;border-left:1px solid var(--line);display:flex;align-items:center;justify-content:center}

/* welcome */
.welcome-bar{left:129px;top:158px;width:941px;height:45px;background:linear-gradient(#555,#252525);color:#fff;font-size:17px;padding:13px 20px;border-radius:2px}
.welcome{left:129px;top:202px;width:941px;height:174px;background:var(--card);border:1px solid var(--line);border-top:0}
.welcome .photo{position:absolute;left:15px;top:20px;width:216px;height:128px;border-radius:2px;background:linear-gradient(120deg,#d7c3aa,#6e8fbf 45%,#c59b78 80%)}
.welcome .copy{position:absolute;left:254px;top:20px;width:670px;font-size:12.5px;line-height:18px;color:#808080}
.welcome .copy p+p{margin-top:20px}

/* section columns */
.col-head{top:408px;width:302px;height:44px;border-radius:3px;background:linear-gradient(var(--blue-top),var(--navy));color:#fff;font-size:16px;display:flex;align-items:center;padding:0 14px 0 16px;gap:12px}
.col-head .more{margin-left:auto}
.card{width:302px;height:100px;background:var(--card);border:1px solid var(--line);border-radius:2px;padding:12px 18px;font-size:13px;line-height:18px}
.card .date{color:var(--orange);font-size:12px;margin-top:5px}
.card .source{color:var(--blue);font-size:12px;margin-top:1px}
.card.blog{display:flex;gap:16px;padding:14px 15px}
.thumb{flex:0 0 61px;height:61px;margin-top:3px}

/* lower boxes */
.box{top:788px;width:302px;height:175px;background:var(--card);border:1px solid var(--line);border-radius:2px;padding:14px 8px 10px 16px}
.box-title{display:flex;align-items:center;gap:12px;color:var(--green);font-size:20px;font-weight:400;line-height:28px}
.box .q{color:var(--navy);font-size:12.5px;line-height:18px;margin-top:10px}
.box .a{font-size:12.5px;line-height:17px;margin-top:4px}
.box .date{color:var(--orange);font-size:12.5px;line-height:17px;margin-top:4px}
.stats{display:flex;margin-top:14px}
.stats ul{list-style:none;flex:1;font-size:12.5px;color:var(--dark);line-height:25px;padding-left:4px}
.stats ul+ul{border-left:1px solid var(--line);padding-left:46px}
.stats span{color:var(--blue)}

.links{left:129px;top:987px;width:941px;height:166px;background:var(--card);border:1px solid var(--line);border-radius:2px}
.links .box-title{position:absolute;left:26px;top:18px}
.link-col{position:absolute;top:62px;list-style:none;font-size:12.5px;color:var(--dark);line-height:25px}
.link-col li::before{content:"»";margin-right:7px;color:#666}

/* footer */
.footer{left:0;top:1185px;width:1200px;height:106px;background:var(--footer)}
.foot-nav{position:absolute;left:131px;top:28px;font-size:13px;color:var(--white);display:flex}
.foot-nav .sep{margin:0 16px 0 8px;color:var(--white)}
.copyright{position:absolute;left:131px;top:59px;font-size:13px;color:var(--white)}
.social{position:absolute;left:906px;top:36px;display:flex;gap:11px;align-items:center}
.social .tile{width:24px;height:24px;border-radius:4px;background:#d8d8d8}
</style>
</head>
<body>
<div class="stage">

  <header>
    <a class="brand abs" href="#"><span class="brand-mark"></span><span class="brand-name">Harbor<br>Guidance<br>Portal</span></a>
    <nav class="topnav abs">
      <a class="current" href="#"><svg width="14" height="13" viewBox="0 0 14 13"><path d="M7 0 0 6.5h2V13h3.5V9h3v4H12V6.5h2z" fill="#333"/></svg>Home</a><span class="sep">|</span>
      <a href="#"><svg width="14" height="11" viewBox="0 0 14 11" fill="#333"><rect width="3" height="2.4"/><rect x="4" width="10" height="2.4"/><rect y="4.3" width="3" height="2.4"/><rect x="4" y="4.3" width="10" height="2.4"/><rect y="8.6" width="3" height="2.4"/><rect x="4" y="8.6" width="10" height="2.4"/></svg>Menu</a><span class="sep">|</span>
      <a href="#"><svg width="14" height="14" viewBox="0 0 14 14"><circle cx="7" cy="7" r="5.5" fill="none" stroke="#333" stroke-width="3"/><path d="M2 2l3 3M12 2 9 5M2 12l3-3M12 12 9 9" stroke="#fff" stroke-width="1.4"/></svg>Game</a><span class="sep">|</span>
      <a href="#"><svg width="11" height="14" viewBox="0 0 11 14"><path d="M0 0h7l4 4v10H0z" fill="#333"/><path d="M2 6h7M2 8.5h7M2 11h7" stroke="#fff"/></svg>Care Hub</a>
    </nav>
    <div class="search abs">Search here...<span class="go"><svg width="18" height="18" viewBox="0 0 18 18"><circle cx="7" cy="7" r="5.5" fill="none" stroke="#333" stroke-width="1.6"/><path d="M11 11l6 6" stroke="#333" stroke-width="2.4"/></svg></span></div>
    <div class="notify abs"><span class="count">1</span>427</div>
    <div class="user abs"><span class="avatar" role="img" aria-label="User profile photo"></span>Dana Brooks<span class="caret"><svg width="9" height="5" viewBox="0 0 9 5"><path d="M0 0h9L4.5 5z" fill="#aaa"/></svg></span></div>
  </header>

  <div class="welcome-bar abs">Welcome to the Harbor Guidance Portal</div>
  <section class="welcome abs">
    <div class="photo" role="img" aria-label="Photo of a lab technician examining a sample"></div>
    <div class="copy">
      <p>Lorem ipsum dolor sit amet, consectetur adipisicing elit, sed do eiusmod tempor incididunt ut labore et dolore magna aliqua. Ut enim ad minim veniam, quis nostrud exercitation ullamco laboris nisi ut aliquip ex ea commodo consequat. Duis aute irure dolor in reprehenderit in voluptate velit esse cillum dolore eu fugiat nulla pariatur. Excepteur sint occaecat cupid-atat non proident, sunt in culpa qui officia deserunt mollit anim id est laborum.</p>
      <p>Sed ut perspiciatis unde omnis iste natus error sit voluptatem accusantium doloremque laudantium, totam rem aperiam, eaque ipsa quae ab illo inventore veritatis et quasi architecto beatae vitae dicta sunt explicabo.</p>
    </div>
  </section>

  <!-- Compliance News -->
  <div class="col-head abs" style="left:129px"><svg width="22" height="16" viewBox="0 0 22 16"><rect x="1" y="1" width="20" height="14" fill="none" stroke="#fff" stroke-width="1.5"/><path d="M4 5h14M4 8h6M4 11h6M12 8h6v3h-6z" stroke="#fff" stroke-width="1.3" fill="none"/></svg>Compliance News<svg class="more" width="17" height="13" viewBox="0 0 17 13"><path d="M1 1l5 5.5L1 12M9 1l5 5.5L9 12" fill="none" stroke="#fff" stroke-width="2"/></svg></div>
  <div class="card abs" style="left:129px;top:455px">Excepteur sint occaecat cupidatat non proident, sunt in culpa qui officia deserunt.<div class="date">15 Nov 2013</div><div class="source">HRA News - Pharma Sector Daily</div></div>
  <div class="card abs" style="left:129px;top:559px">Excepteur sint occaecat cupidatat non proident, sunt in culpa qui officia deserunt.<div class="date">15 Nov 2013</div><div class="source">HRA News - Pharma Sector Daily</div></div>
  <div class="card abs" style="left:129px;top:663px">Excepteur sint occaecat cupidatat non proident, sunt in culpa qui officia deserunt.<div class="date">15 Nov 2013</div><div class="source">HRA News - Pharma Sector Daily</div></div>

  <!-- Compliance Blog -->
  <div class="col-head abs" style="left:449px"><svg width="20" height="18" viewBox="0 0 20 18"><path d="M0 0h20v12H9l-5 5v-5H0z" fill="#fff"/></svg>Compliance Blog<svg class="more" width="17" height="13" viewBox="0 0 17 13"><path d="M1 1l5 5.5L1 12M9 1l5 5.5L9 12" fill="none" stroke="#fff" stroke-width="2"/></svg></div>
  <div class="card blog abs" style="left:449px;top:455px"><div class="thumb" role="img" aria-label="Test tubes with green liquid" style="background:linear-gradient(#f2f2f2,#9fd43a)"></div><div>Duis aute irure dolor in reprehen-derit in voluptate velit esse cillum dolore eu fugiat nulla pariatur.<div class="date">15 Nov 2013</div></div></div>
  <div class="card blog abs" style="left:449px;top:559px"><div class="thumb" role="img" aria-label="Beakers with coloured liquids" style="background:linear-gradient(120deg,#3d2d2a,#c86a2b 50%,#2fb08d)"></div><div>Duis aute irure dolor in reprehen-derit in voluptate velit esse cillum dolore eu fugiat nulla pariatur.<div class="date">15 Nov 2013</div></div></div>
  <div class="card blog abs" style="left:449px;top:663px"><div class="thumb" role="img" aria-label="Laboratory flask with blue liquid" style="background:linear-gradient(#d9dcdc,#2ea9c7)"></div><div>Duis aute irure dolor in reprehen-derit in voluptate velit esse cillum dolore eu fugiat nulla pariatur.<div class="date">15 Nov 2013</div></div></div>

  <!-- Forms -->
  <div class="col-head abs" style="left:769px"><svg width="18" height="19" viewBox="0 0 18 19"><rect x="1" y="1" width="16" height="17" fill="none" stroke="#fff" stroke-width="1.6"/><path d="M4 5h2M8 5h6M4 9h2M8 9h6M4 13h2M8 13h6" stroke="#fff" stroke-width="1.5"/></svg>Forms<svg class="more" width="17" height="13" viewBox="0 0 17 13"><path d="M1 1l5 5.5L1 12M9 1l5 5.5L9 12" fill="none" stroke="#fff" stroke-width="2"/></svg></div>
  <div class="card abs" style="left:769px;top:455px">Excepteur sint occaecat cupidatat non proident, sunt in culpa qui officia deserunt.<div class="date">15 Nov 2013</div><div class="source">HRA News - Pharma Sector Daily</div></div>
  <div class="card abs" style="left:769px;top:559px">Excepteur sint occaecat cupidatat non proident, sunt in culpa qui officia deserunt.<div class="date">15 Nov 2013</div><div class="source">HRA News - Pharma Sector Daily</div></div>
  <div class="card abs" style="left:769px;top:663px">Excepteur sint occaecat cupidatat non proident, sunt in culpa qui officia deserunt.<div class="date">15 Nov 2013</div><div class="source">HRA News - Pharma Sector Daily</div></div>

  <!-- FAQ -->
  <section class="box abs" style="left:129px">
    <h2 class="box-title"><svg width="21" height="21" viewBox="0 0 21 21"><rect width="21" height="21" rx="3" fill="#55a51f"/><path d="M7 8a3.5 3.5 0 1 1 5 3c-1.2.6-1.5 1.2-1.5 2.5" fill="none" stroke="#fff" stroke-width="2.2"/><rect x="9.3" y="15" width="2.4" height="2.4" fill="#fff"/></svg>FAQ</h2>
    <p class="q">Q - Excepteur sint occaecat cupidatat non proide nt, sunt in culpa qui officia deserunt.</p>
    <p class="a">Duis aute irure dolor in reprehenderit in voluptate velit esse cillum dolore eu fugiat nulla pariatur.</p>
    <p class="date">15 Nov 2013</p>
  </section>

  <!-- Document Library -->
  <section class="box abs" style="left:450px">
    <h2 class="box-title"><svg width="16" height="21" viewBox="0 0 16 21"><path d="M0 0h10l6 6v15H0z" fill="#55a51f"/><path d="M3 9h10M3 12h10M3 15h10" stroke="#fff" stroke-width="1.4"/></svg>Document Library</h2>
    <p class="q">Excepteur sint occaecat cupidatat non proide nt, sunt in culpa qui officia deserunt.</p>
    <p class="a">Duis aute irure dolor in reprehenderit in voluptate velit esse cillum dolore eu fugiat nulla pariatur.</p>
    <p class="date">15 Nov 2013</p>
  </section>

  <!-- Reports -->
  <section class="box abs" style="left:770px;padding:14px 12px">
    <h2 class="box-title"><svg width="21" height="21" viewBox="0 0 21 21"><rect x="1" y="2" width="19" height="12" fill="none" stroke="#55a51f" stroke-width="1.6"/><path d="M4 11l4-4 3 3 5-5M10 14v3M6 20l4-3 4 3" fill="none" stroke="#55a51f" stroke-width="1.6"/></svg>Reports</h2>
    <div class="stats">
      <ul><li>Player : <span>Alex.K</span></li><li>Rank : <span>4</span></li><li>Score : <span>456</span></li><li>% : <span>88%</span></li></ul>
      <ul><li>Player : <span>Alex.K</span></li><li>Rank : <span>4</span></li><li>Score : <span>456</span></li><li>% : <span>88%</span></li></ul>
    </div>
  </section>

  <!-- Relevant links -->
  <section class="links abs">
    <h2 class="box-title"><svg width="24" height="24" viewBox="0 0 24 24"><g fill="none" stroke="#55a51f" stroke-width="3"><rect x="2" y="10" width="11" height="7" rx="3.5" transform="rotate(-45 7.5 13.5)"/><rect x="11" y="7" width="11" height="7" rx="3.5" transform="rotate(-45 16.5 10.5)"/></g></svg>Relevank links</h2>
    <ul class="link-col" style="left:30px"><li>Donec tincidunt</li><li>Donec et urna tellus</li><li>Aenean consectetur</li></ul>
    <ul class="link-col" style="left:223px"><li>Quisque vestibulum</li><li>Quisque</li><li>Proin ultricies urna</li></ul>
    <ul class="link-col" style="left:435px"><li>Fusce vel</li><li>Aenean pretium risus</li><li>Mauris dictum</li></ul>
    <ul class="link-col" style="left:619px"><li>Curabitur sed</li><li>Morbi semper</li><li>Donec eget porta</li></ul>
    <ul class="link-col" style="left:782px"><li>Class aptent taciti</li><li>Phasellus dapibus eros</li><li>Nulla eget</li></ul>
  </section>

  <footer class="footer abs">
    <nav class="foot-nav"><a href="#">Home</a><span class="sep">|</span><a href="#">Menu</a><span class="sep">|</span><a href="#" style="margin-left:8px">Game</a><span class="sep" style="margin-left:14px">|</span><a href="#">Care Hub</a></nav>
    <p class="copyright">(c) 2013 Harbor Guidance Portal. All Right Reserved.</p>
    <div class="social">
      <span class="tile"></span><span class="tile"></span><span class="tile" style="border-radius:50%"></span><span class="tile"></span>
      <svg width="26" height="20" viewBox="0 0 26 20"><rect x="1" y="1" width="24" height="18" fill="none" stroke="#d8d8d8" stroke-width="2"/><path d="M1 1l12 10L25 1" fill="none" stroke="#d8d8d8" stroke-width="2"/></svg>
    </div>
  </footer>

</div>
</body>
</html>
```